I would like a single page website for Skyward Rentals Pacific. In the file list provided there is basic information to be included as well as our logo with colors, fonts and images to be included.
Site must be very simple and be able to be loaded onto smart phones etc very quickly.
Site needs to be very smart in appearance

Target Market(s)

All prospective drone customers from Police to Parties.

Industry/Entity Type

Hire

Requirements
Must have
• Must have variation of color schemes supplied
Nice to have
• Must be very eye catching without going over the top
Should not have
• Anything slow to load.

```html
<!DOCTYPE html>
<html lang="en">
<head>
<meta charset="utf-8">
<title>Skyward Rentals Pacific</title>
<link rel="stylesheet" href="https://fonts.googleapis.com/css2?family=Exo+2:wght@600&family=Open+Sans:wght@400;600;700&family=Ubuntu:wght@400;500;700&display=swap">
<style>
:root{
  --navy:#0f1f8a;
  --navy-dark:#0a1566;
  --text:#3a3a3a;
  --muted:#555;
  --rule:#d6d6d6;
  --bar:#c9c9cc;
  --footer:#000;
  --footer-base:#0b0b0b;
  --footer-text:#cfcfcf;
  --accent:#f2b51c;
}
*{box-sizing:border-box;margin:0;padding:0}
html,body{width:840px;height:1200px;overflow:hidden;background:#fff}
body{position:relative;font-family:"Open Sans",Arial,sans-serif;color:var(--text)}
.topline{position:absolute;left:0;top:0;width:840px;height:3px;background:var(--bar)}
.contact-tab{position:absolute;left:642px;top:3px;width:128px;height:18px;background:var(--bar);color:#fff;font-size:8px;line-height:18px;text-align:center;letter-spacing:.2px}
.brand{position:absolute;left:78px;top:22px;display:flex;align-items:center;gap:7px;font-family:"Ubuntu",sans-serif;font-weight:700;color:var(--navy);font-size:14px;line-height:16px;letter-spacing:.5px}
.brand .dot{width:14px;height:14px;border-radius:50%;background:var(--navy)}
.nav{position:absolute;top:36px;left:404px;display:flex;gap:23px;font-family:"Ubuntu",sans-serif;font-weight:500;font-size:11px;color:var(--navy)}
.hero{position:absolute;left:0;top:74px;width:840px;height:336px;background:radial-gradient(ellipse at 30% 40%,#5a5246 0%,#2b2823 45%,#111 100%)}
.hero-drone{position:absolute;left:490px;top:104px;width:250px;height:150px;background:radial-gradient(ellipse,#e9eaec 0%,#b7b9bd 40%,rgba(80,80,80,0) 72%)}
.hero h1{position:absolute;left:108px;top:130px;width:340px;font-family:"Exo 2",sans-serif;font-weight:600;font-size:22px;line-height:27px;color:#fff;letter-spacing:.6px}
.hero-arrows{position:absolute;left:110px;top:254px}
.card{position:absolute;top:422px;width:214px}
.card .photo{width:214px;height:138px;border:1px solid #ccc}
.card h2{font-family:"Ubuntu",sans-serif;font-weight:400;font-size:16px;color:var(--navy);margin-top:8px}
.card p{font-size:8.5px;line-height:10px;color:var(--muted);margin-top:4px;padding-left:1px}
.rule{position:absolute;left:69px;top:618px;width:702px;height:1px;background:var(--rule)}
.welcome{position:absolute;left:69px;top:632px;width:445px}
.welcome h2{font-family:"Ubuntu",sans-serif;font-weight:400;font-size:15px;color:var(--navy)}
.welcome p{font-size:8.6px;line-height:14.4px;margin-top:9px;text-align:justify}
.video{position:absolute;left:69px;top:754px;width:463px;height:220px;background:linear-gradient(120deg,#8f9d55 0%,#556b35 40%,#324a26 70%,#b9c6cf 100%)}
.vsep{position:absolute;left:547px;top:624px;width:1px;height:352px;background:#e3e3e3}
.featured{position:absolute;left:559px;top:640px;width:200px}
.featured h2{font-family:"Ubuntu",sans-serif;font-weight:400;font-size:16px;color:var(--navy);margin-bottom:8px}
.featured ul{list-style:none;margin-left:6px;width:191px}
.featured li{position:relative;font-size:8.5px;line-height:14px;padding:6px 0 8px 7px;border-bottom:1px dashed #999;color:var(--muted)}
.featured li::before{content:"";position:absolute;left:-2px;top:11px;width:3px;height:3px;border-right:1px solid #666;border-top:1px solid #666;transform:rotate(45deg)}
.footer{position:absolute;left:0;top:985px;width:840px;height:215px;background:var(--footer);color:var(--footer-text)}
.footer-nav{position:absolute;top:20px;width:840px;display:flex;justify-content:center;gap:20px;font-size:8.5px;letter-spacing:.2px}
.fcol{position:absolute;top:62px;font-size:8.5px;line-height:11px}
.fcol h3{font-size:10px;font-weight:700;color:#ddd;margin-bottom:9px}
.fcol .caps{font-size:7px;line-height:11px;text-transform:uppercase}
.more{color:var(--accent);font-size:9px;margin-top:10px;display:flex;align-items:center;gap:6px}
.more i{width:6px;height:6px;border-radius:50%;background:#999;display:inline-block}
.social{display:flex;gap:6px}
.social span{width:17px;height:17px;border-radius:2px}
.footer-base{position:absolute;left:0;bottom:0;width:840px;height:40px;background:var(--footer-base);font-size:7px;line-height:40px;text-align:center;color:#bbb}
</style>
</head>
<body>
<div class="topline"></div>
<div class="contact-tab">0400 217 395 &nbsp;|&nbsp; CONTACT</div>
<div class="brand"><span class="dot"></span><span>SKYWARD RENTALS<br>PACIFIC</span></div>
<nav class="nav"><span>Home</span><span>About</span><span>Services</span><span>Blog</span><span>Testimonials</span><span>Contact Us</span></nav>

<section class="hero" role="img" aria-label="Blurred night city lights with a white camera drone hovering">
  <div class="hero-drone"></div>
  <h1>We give drones on hire for parties, surveillance, security etc..</h1>
  <svg class="hero-arrows" width="40" height="26" viewBox="0 0 40 26"><path d="M12 2 2 13l10 11M26 2l10 11-10 11" fill="none" stroke="#fff" stroke-width="1.2"/></svg>
</section>

<div class="card" style="left:69px"><div class="photo" role="img" aria-label="Children celebrating at a birthday party with balloons" style="background:linear-gradient(135deg,#e8557a,#f3c24a 50%,#7bb6e0)"></div><h2>Special Occasions</h2><p>Children's Birthday Parties, Weddings</p></div>
<div class="card" style="left:313px"><div class="photo" role="img" aria-label="Runners in a city marathon" style="background:linear-gradient(180deg,#6f6a66,#3d3a39 60%,#8a8580)"></div><h2 style="margin-left:5px">Sporting events</h2><p style="margin-left:5px">4K Video of yourself participating in marathons etc</p></div>
<div class="card" style="left:557px"><div class="photo" role="img" aria-label="Construction workers in hard hats at a building site" style="background:linear-gradient(160deg,#2a5fb0,#6e9ad0 45%,#8a7a55 80%,#c2d84a)"></div><h2 style="margin-left:2px">Real Estate Brochures</h2><p style="margin-left:2px">Construction project updates for remote stake holders</p></div>

<div class="rule"></div>

<section class="welcome">
  <h2>Welcome To Our Website</h2>
  <p>Sed ut perspiciatis unde omnis iste natus error sit voluptatem accusantium doloremque laudantium, totam rem aperiam, eaque ipsa quae ab illo inventore veritatis et quasi architecto beatae vitae dicta sunt explicabo. Nemo enim ipsam voluptatem quia voluptas sit aspernatur aut odit aut fugit, sed quia consequuntur magni dolores eos qui ratione voluptatem sequi nesciunt. Neque porro quisquam est, qui dolorem ipsum quia dolor sit amet, consectetur, adipisci velit, sed quia non numquam eius modi tempora incidunt ut labore et dolore magnam aliquam quaerat voluptatem. Ut enim ad minima veniam,</p>
</section>
<div class="video" role="img" aria-label="Video: multirotor drone flying over green trees">
  <svg width="463" height="220" viewBox="0 0 463 220"><circle cx="217" cy="114" r="30" fill="rgba(0,0,0,.35)"/><path d="M211 100v28l19-14z" fill="#fff"/></svg>
</div>

<div class="vsep"></div>
<aside class="featured">
  <h2>Featured Services</h2>
  <ul>
    <li>Special Occasions, Children's Birthday Parties, Weddings</li>
    <li>Sporting events –4K Video of yourself participating in marathons etc</li>
    <li>Real Estate Brochures</li>
    <li>Construction project updates for remote stake holders</li>
    <li>Surveillance – Police, Local councilsworksafeetc</li>
    <li>Building/Roof Condition Inspections</li>
    <li>Lost pets</li>
    <li>Accident reconstructions</li>
    <li>Insurance assessing</li>
  </ul>
</aside>

<footer class="footer">
  <nav class="footer-nav"><span>HOME</span><span>ABOUT US</span><span>SERVICES</span><span>BLOG</span><span>TESTIMONIALS</span><span>CONTACT US</span></nav>
  <div class="fcol" style="left:110px">
    <h3><svg width="7" height="9" viewBox="0 0 7 9" style="margin-right:5px"><path d="M3.5 0A3.2 3.2 0 0 0 .3 3.2C.3 5.6 3.5 9 3.5 9s3.2-3.4 3.2-5.8A3.2 3.2 0 0 0 3.5 0z" fill="#ccc"/><circle cx="3.5" cy="3.2" r="1.1" fill="#000"/></svg>Contact Us</h3>
    <p>14 Harbour Lane Ste 210<br>Brisbane<br>QLD 4000-1120</p>
    <p style="margin-top:13px"><svg width="9" height="7" viewBox="0 0 9 7" style="margin-right:6px"><rect x=".5" y=".5" width="8" height="6" fill="none" stroke="#ccc"/><path d="M.5.5 4.5 4l4-3.5" fill="none" stroke="#ccc"/></svg>info@skywardrentals.net</p>
  </div>
  <div class="fcol" style="left:356px;width:170px">
    <h3>Most Popular</h3>
    <p style="font-size:7.5px">VERITIASER MIUATSA UYAGSASA</p>
    <p class="caps" style="margin-top:12px">Lorem ipsum dolor sit amet, consectetur adipiscing elit. Sed blandit massa vel mauris sollicitudin...</p>
    <div class="more">more <i></i></div>
  </div>
  <div class="fcol" style="left:595px">
    <h3>Follow Us</h3>
    <div class="social"><span style="background:#3b5998"></span><span style="background:#3fa9d8"></span><span style="background:#2f6fa8"></span><span style="background:#e6e6e6"></span><span style="background:#a17c5a"></span><span style="background:#555"></span><span style="background:#cb2027"></span></div>
  </div>
  <div class="footer-base">© 2015 • www.skywardrentals.net • PRIVACY POLICY</div>
</footer>
</body>
</html>
```